Corporate Business Card

Very professional, Modern, Not to busy, include phone address email, website
(541) 617-4930, 18761 52nd Avenue S, Alder Falls, OR 98047, martin@plumlinegroup.com, varkoworks.com

Target Market(s)

Manufacturing

Industry/Entity Type

Aero, machining, manufacturing, Off road racing

Contact Information for Business Card

Phone, address email, website

```html
<!DOCTYPE html>
<html lang="en">
<head>
<meta charset="utf-8">
<title>Varko Works – Business Card</title>
<link rel="stylesheet" href="https://fonts.googleapis.com/css2?family=Poppins:wght@400;500;600;700&display=swap">
<style>
  :root {
    --bg: #1f1f21;
    --navy: #173468;
    --navy-deep: #122a56;
    --navy-light: #1e4488;
    --red: #d8212b;
    --white: #ffffff;
  }
  * { box-sizing: border-box; margin: 0; padding: 0; }
  html, body {
    width: 1200px; height: 1108px; overflow: hidden;
    background: var(--bg);
    font-family: "Poppins", sans-serif;
  }
  .stage {
    width: 1200px; height: 1108px;
    display: flex; align-items: center; justify-content: center; gap: 60px;
  }
  .card {
    width: 420px; height: 720px;
    border-radius: 22px;
    background: var(--navy);
    position: relative;
    overflow: hidden;
    color: var(--white);
  }
  .card-front { display: flex; flex-direction: column; align-items: center; }
  .brand {
    margin-top: 150px;
    display: flex; align-items: center; gap: 14px;
  }
  .brand-mark { width: 22px; height: 22px; background: var(--red); flex: none; }
  .brand-name {
    font-size: 42px; font-weight: 700; letter-spacing: 1px;
    color: var(--white); line-height: 1; white-space: nowrap;
  }
  .person { margin-top: 170px; text-align: center; }
  .person-name {
    color: var(--red); font-weight: 600; font-size: 30px;
    text-transform: uppercase; letter-spacing: 1px; line-height: 1.1;
  }
  .person-title { font-size: 19px; font-weight: 400; margin-top: 2px; }
  .icon-row {
    margin-top: 22px; width: 300px;
    display: flex; align-items: center; gap: 8px;
  }
  .icon-row .rule { flex: 1; height: 1.5px; background: var(--white); }
  .icon {
    width: 30px; height: 30px; border-radius: 5px; background: var(--red);
    display: flex; align-items: center; justify-content: center;
  }
  .icon svg { width: 18px; height: 18px; }
  .contact { margin-top: 12px; text-align: center; font-size: 19px; line-height: 1.4; }
  .divider { width: 300px; height: 1.5px; background: var(--white); margin: 20px 0 18px; }
  .address { text-align: center; font-size: 19px; line-height: 1.35; font-style: normal; }
  .back-pattern {
    position: absolute; inset: 0;
    background: linear-gradient(160deg, var(--navy-light) 0%, var(--navy) 45%, var(--navy-deep) 100%);
  }
  .back-brand {
    position: absolute; left: 0; right: 0; top: 470px;
    display: flex; align-items: center; justify-content: center; gap: 10px;
  }
  .back-brand .brand-mark { width: 14px; height: 14px; }
  .back-brand .brand-name { font-size: 28px; }
</style>
</head>
<body>
<main class="stage">
  <section class="card card-front">
    <div class="brand">
      <span class="brand-mark"></span>
      <span class="brand-name">VARKO WORKS</span>
    </div>

    <div class="person">
      <h1 class="person-name">Daniel Reyes</h1>
      <p class="person-title">Managing Director</p>
    </div>

    <div class="icon-row">
      <span class="rule"></span>
      <span class="icon" aria-label="Phone">
        <svg viewBox="0 0 24 24" fill="#fff"><path d="M6.6 10.8a15.1 15.1 0 0 0 6.6 6.6l2.2-2.2c.3-.3.7-.4 1-.2 1.1.4 2.300.6 3.6.6.6 0 1 .4 1 1V20c0 .6-.4 1-1 1A17 17 0 0 1 3 4c0-.6.4-1 1-1h3.5c.6 0 1 .4 1 1 0 1.3.2 2.5.6 3.6.1.3 0 .7-.2 1z"/></svg>
      </span>
      <span class="icon" aria-label="Email">
        <svg viewBox="0 0 24 24" fill="none" stroke="#fff" stroke-width="2"><rect x="3" y="5" width="18" height="14" rx="1"/><path d="M3 6l9 7 9-7"/></svg>
      </span>
      <span class="icon" aria-label="Website">
        <svg viewBox="0 0 24 24" fill="none" stroke="#fff" stroke-width="2"><circle cx="12" cy="12" r="9"/><path d="M3 12h18M12 3c3 3 3 15 0 18M12 3c-3 3-3 15 0 18"/></svg>
      </span>
      <span class="rule"></span>
    </div>

    <div class="contact">
      <p>(541) 617-4930</p>
      <p>martin@plumlinegroup.com</p>
      <p>www.varkoworks.com</p>
    </div>

    <div class="divider"></div>

    <address class="address">
      18761 52nd Avenue S<br>
      Alder Falls, OR 98047
    </address>
  </section>

  <section class="card card-back">
    <div class="back-pattern" role="img" aria-label="Tone-on-tone embossed repeat of the company name across the card"></div>
    <div class="back-brand">
      <span class="brand-mark"></span>
      <span class="brand-name">VARKO WORKS</span>
    </div>
  </section>
</main>
</body>
</html>
```